Heritage Hollow Business Cards

Require a business card design. <br/><br/>Needs to include logo (either round or long version) plus these details:<br/>Maya Torvell<br/>Heritage Hollow<br/>maya@kelvadtrading.com.au<br/>02 6481 7395<br/>PO Box Glenwarra NSW 2791<br/>www.heritagehollow.com.au<br/><br/>I need in an editable format so that I can create for multiple staff members. <br/><br/>

Target Market(s)

We are an online store selling renovation products to home owners are builders. Looking for a classic classy design.

Industry/Entity Type

Home And Garden

Contact Information for Business Card

Maya Torvell
Heritage Hollow
maya@kelvadtrading.com.au
02 6481 7395
PO Box Glenwarra NSW 2791
www.heritagehollow.com.au

Colors

Designer to choose colors to be used in the design.

Requirements
Must have
• Must include Logo.

```html
<!DOCTYPE html>
<html lang="en">
<head>
<meta charset="utf-8">
<title>Heritage Hollow Business Cards</title>
<link href="https://fonts.googleapis.com/css2?family=Work+Sans:wght@400;500;600&display=swap" rel="stylesheet">
<style>
  :root {
    --backdrop: #d4d4d4;
    --card-light: #ffffff;
    --card-dark: #1e1e1e;
    --ink: #1a1a1a;
    --ink-soft: #555555;
    --rule: #3a3a3a;
    --ring-light: #6a6a6a;
    --ring-dark: #bdbdbd;
    --paper-text: #f2f2f2;
  }
  * { margin: 0; padding: 0; box-sizing: border-box; }
  html, body {
    width: 1200px;
    height: 1001px;
    overflow: hidden;
    background: var(--backdrop);
    font-family: "Work Sans", Arial, sans-serif;
  }
  .card {
    position: absolute;
    left: 306px;
    width: 587px;
    height: 336px;
    box-shadow: 0 3px 8px rgba(0,0,0,0.25);
  }
  .card--front { top: 134px; background: var(--card-light); color: var(--ink); }
  .card--back { top: 524px; background: var(--card-dark); color: var(--paper-text); }

  .brand-mark {
    position: absolute;
    border-radius: 50%;
    display: flex;
    align-items: center;
    justify-content: center;
    text-align: center;
    font-weight: 500;
    line-height: 1.1;
  }
  .card--front .brand-mark {
    left: 384px; top: 36px; width: 156px; height: 156px;
    border: 1px solid var(--ring-light);
    font-size: 22px;
    color: var(--ink);
  }
  .card--back .brand-mark {
    left: 191px; top: 49px; width: 220px; height: 220px;
    border: 1px solid var(--ring-dark);
    font-size: 30px;
    color: var(--paper-text);
  }

  .holder-name {
    position: absolute; left: 37px; top: 184px;
    font-size: 25px; font-weight: 600; letter-spacing: 0.5px;
  }
  .holder-role {
    position: absolute; left: 37px; top: 215px;
    font-size: 14px; color: var(--ink-soft);
  }
  .holder-rule {
    position: absolute; left: 106px; top: 225px;
    width: 447px; height: 1px; background: var(--rule);
  }
  .contact-list {
    position: absolute; left: 35px; top: 247px;
    list-style: none;
    font-size: 14.5px; color: var(--ink-soft);
  }
  .contact-list li {
    display: flex; align-items: center; gap: 7px;
    height: 20px;
  }
  .contact-icon { width: 13px; height: 13px; flex: none; }
  .web strong { font-weight: 500; color: var(--ink-soft); }
  .postal {
    position: absolute; left: 416px; top: 267px;
    font-size: 14.5px; color: var(--ink-soft); line-height: 20px;
    font-style: normal;
  }
  .back-web {
    position: absolute; left: 0; right: 0; top: 286px;
    text-align: center;
    font-size: 15px; letter-spacing: 2.6px;
  }
  .back-web strong { font-weight: 600; }
</style>
</head>
<body>
  <section class="card card--front" aria-label="Business card front">
    <div class="brand-mark">Heritage<br>Hollow</div>
    <h1 class="holder-name">Maya Torvell</h1>
    <p class="holder-role">Director</p>
    <div class="holder-rule"></div>
    <ul class="contact-list">
      <li>
        <svg class="contact-icon" viewBox="0 0 13 13" aria-hidden="true">
          <rect width="13" height="13" rx="2.5" fill="#1a1a1a"/>
          <path d="M4 3.2l1.4 1.7-.8.9c.5 1.1 1.4 2 2.5 2.5l.9-.8 1.7 1.4-.9 1.1C6.4 9.7 3.3 6.6 3 4.1z" fill="#fff"/>
        </svg>
        02 6481 7395
      </li>
      <li>
        <svg class="contact-icon" viewBox="0 0 13 13" aria-hidden="true">
          <rect width="13" height="13" rx="2.5" fill="#1a1a1a"/>
          <rect x="3" y="4" width="7" height="5" fill="none" stroke="#fff" stroke-width="1"/>
          <path d="M3 4l3.5 2.7L10 4" fill="none" stroke="#fff" stroke-width="1"/>
        </svg>
        maya@kelvadtrading.com.au
      </li>
      <li class="web">
        <svg class="contact-icon" viewBox="0 0 13 13" aria-hidden="true">
          <rect width="13" height="13" rx="2.5" fill="#1a1a1a"/>
          <circle cx="6.5" cy="6.5" r="3.5" fill="none" stroke="#fff" stroke-width="1"/>
          <path d="M3 6.5h7M6.5 3c-1.5 2-1.5 5 0 7M6.5 3c1.5 2 1.5 5 0 7" fill="none" stroke="#fff" stroke-width=".8"/>
        </svg>
        <span>www.<strong>heritagehollow</strong>.com.au</span>
      </li>
    </ul>
    <address class="postal">PO Box Glenwarra<br>NSW 2791</address>
  </section>

  <section class="card card--back" aria-label="Business card back">
    <div class="brand-mark">Heritage<br>Hollow</div>
    <p class="back-web">www.<strong>heritagehollow</strong>.com.au</p>
  </section>
</body>
</html>
```